Healthcare/Medical Consultant Company

QRN is a Healthcare Conultant Company. We help doctors manage the business side of their medical practice.
We already have a very basic world press design. We want an upgraded design that conveys partnership, healthcare expertise and healthcare innovation to our client. It needs to have a sleek, clean, modern and inclusive look. Pictures need need to convey diversity (including pictures of people of all races and shows both men and women working together in a healthcare environment to make it better). The Pictures on the home page should particularly illustrate diversity and Healthcare expertise. The company logo is blue and white but the site doesn’t have to follow the exact same theme but the logo needs to blend well with the chosen theme. The logo should ideally be in the header of the website. We would also like the following included in our website:

1. Pages should include: a home page, About Us page, Services page, Get a quote page, Contact Us page, Staff page(where we can add pictures and bio for staff).

2. The Drop down menu for services should have hyperlinks ( for each service)Leading to a page that provides detailed info about that specific service. Our services include: Revenue Cycle Management, Regulatory Compliance, Human Resources Management, & practice Management.

3. Links to social media should in the header or footer of each page.

4. Contact info should be in the footer of each page.

5. Clients should be an email to us from the contact page.

Target Market(s)

Physician Medical Practices

Industry/Entity Type

Medical

Coding

Coded - Design and coding required

Font styles to use
Sans Serif

Colors

Designer to choose colors to be used in the design.

Requirements
Must have
• See project description
Nice to have
• See project description

```html
<!DOCTYPE html>
<html lang="en">
<head>
<meta charset="utf-8">
<title>QRN – Quarnell Health Solutions LLC</title>
<link href="https://fonts.googleapis.com/css2?family=Poppins:wght@400;500;600&family=Lato:wght@400;700&display=swap" rel="stylesheet">
<style>
:root{
  --blue:#0a4f9e;
  --blue-deep:#08468c;
  --sky:#2f93d1;
  --sky-box:#37a5d8;
  --grey-bg:#f5f5f5;
  --line:#d6d6d6;
  --text:#555;
  --dark:#222;
  --white:#fff;
}
*{margin:0;padding:0;box-sizing:border-box}
html,body{width:1200px;height:3622px;overflow:hidden;background:var(--white)}
body{position:relative;font-family:'Lato',sans-serif;color:var(--text);font-size:15px}
a{text-decoration:none}
.abs{position:absolute}
h2.section-title{position:absolute;left:0;width:1200px;text-align:center;font-family:'Poppins',sans-serif;font-weight:600;font-size:27px;color:var(--blue)}
h2.section-title span{color:var(--sky)}

/* header */
.site-header{position:absolute;top:0;left:0;width:1200px;height:106px;background:var(--white);box-shadow:0 2px 6px rgba(0,0,0,.08);z-index:2}
.brand{position:absolute;left:72px;top:22px;display:flex;align-items:center;gap:12px}
.brand-mark{width:22px;height:22px;background:var(--sky)}
.brand-name{font-family:'Poppins',sans-serif;font-weight:600;font-size:34px;color:var(--blue);letter-spacing:1px}
.main-nav a{position:absolute;top:40px;font-family:'Poppins',sans-serif;font-size:15px;color:#444}
.main-nav a.active{color:var(--blue);font-weight:500}
.search-icon{position:absolute;left:1092px;top:38px}

/* hero */
.hero{position:absolute;top:106px;left:0;width:1200px;height:551px;background:linear-gradient(100deg,#3d4146 0%,#6f777d 40%,#8b9499 70%,#5e666c 100%)}
.hero-frame{position:absolute;left:331px;top:111px;width:536px;height:329px;border:4px solid rgba(255,255,255,.75)}
.hero-title{position:absolute;left:0;width:1200px;top:192px;text-align:center;font-family:'Poppins',sans-serif;font-weight:600;font-size:31px;color:var(--white);letter-spacing:.5px}
.hero-sub{position:absolute;left:0;width:1200px;top:256px;text-align:center;font-family:'Poppins',sans-serif;font-size:16px;color:var(--white)}
.btn{display:block;background:var(--blue);color:var(--white);font-family:'Poppins',sans-serif;font-weight:600;font-size:13px;text-align:center;letter-spacing:.4px;text-decoration:none}
.hero .btn{position:absolute;left:533px;top:314px;width:133px;height:39px;line-height:39px}
.hero-dots{position:absolute;top:505px;left:576px;display:flex;gap:5px}
.hero-dots i{width:13px;height:13px;border-radius:50%;border:2px solid var(--white)}
.hero-dots i.on{background:var(--white)}

/* services */
.services-intro{position:absolute;top:780px;left:290px;width:620px;text-align:center;font-size:15px;line-height:30px}
.service-card{position:absolute;width:323px;height:155px;border:1px solid var(--line);text-align:center}
.service-icon{position:absolute;left:124px;top:-37px;width:74px;height:74px;background:var(--blue);border:5px solid var(--white);outline:1px solid var(--blue);display:flex;align-items:center;justify-content:center}
.service-card h3{position:absolute;top:54px;left:0;width:100%;font-family:'Poppins',sans-serif;font-weight:500;font-size:15.5px;color:var(--sky)}
.service-card p{position:absolute;top:84px;left:20px;right:20px;font-size:14.5px;line-height:27px;color:#444}
.service-card p a{color:var(--blue);font-weight:700;text-decoration:underline}

/* about */
.about{position:absolute;top:1347px;left:0;width:1200px;height:415px;background:var(--grey-bg)}
.about-photo{position:absolute;left:0;top:0;width:459px;height:415px;background:linear-gradient(90deg,#d8dde2,#b9c0c7 50%,#eef0f2)}
.about h2{position:absolute;left:524px;top:58px;font-family:'Poppins',sans-serif;font-weight:600;font-size:27px;color:var(--blue)}
.about h2 span{color:var(--sky)}
.about p{position:absolute;left:524px;width:620px;font-size:14.5px;line-height:27px;color:#444}
.about .btn{position:absolute;left:524px;top:314px;width:135px;height:39px;line-height:39px}

/* team */
.team-thumb{position:absolute;top:1890px;width:102px;height:102px;border-radius:50%;border:3px solid #ddd;background:linear-gradient(180deg,#e9ecef,#9aa3ab)}
.team-photo{position:absolute;left:210px;top:2023px;width:208px;height:210px;background:#ddd;padding:10px}
.team-photo div{width:100%;height:100%;background:linear-gradient(180deg,#e6e9ec,#6b7680 70%,#2c3440)}
.team-card{position:absolute;left:423px;top:2047px;width:567px;height:162px;background:var(--grey-bg)}
.team-card h4{position:absolute;left:26px;top:26px;font-family:'Poppins',sans-serif;font-weight:600;font-size:15px;color:var(--blue)}
.team-card .role{position:absolute;left:26px;top:60px;font-weight:700;font-size:14px;color:var(--dark)}
.team-card p{position:absolute;left:26px;top:92px;width:520px;font-size:14.5px;line-height:27px;color:#444}
.team-social{position:absolute;left:196px;top:28px;display:flex;gap:14px}
.team-social i{width:13px;height:13px;border-radius:50%;background:#888}

/* contact */
.contact{position:absolute;top:2293px;left:0;width:1200px;height:423px;background:var(--grey-bg)}
.field{position:absolute;border-bottom:1px solid #c9c9c9;font-size:14px;color:#555;padding-bottom:8px}
.contact .btn{position:absolute;left:531px;top:317px;width:135px;height:39px;line-height:39px;font-size:13px}

/* testimonial */
.quote-shadow{position:absolute;background:#a8d5ee}
.quote-box{position:absolute;left:302px;top:2839px;width:555px;height:263px;background:var(--sky-box);text-align:center;color:var(--white)}
.quote-avatar{position:absolute;left:241px;top:29px;width:74px;height:74px;border-radius:50%;border:4px solid var(--white);background:linear-gradient(180deg,#d9c5b5,#7a5a48)}
.quote-box p{position:absolute;top:128px;left:40px;right:40px;font-size:14.5px;line-height:26px}
.quote-box .author{position:absolute;top:220px;left:0;width:100%;font-family:'Poppins',sans-serif;font-weight:600;font-size:14.5px;color:var(--blue-deep)}
.slide-nav{position:absolute;top:2960px;font-family:'Poppins',sans-serif;font-size:14px}

/* subscribe */
.subscribe{position:absolute;top:3194px;left:0;width:1200px;height:154px;border-top:1px solid #eee}
.subscribe h2{position:absolute;left:80px;top:36px;font-family:'Poppins',sans-serif;font-weight:600;font-size:27px;color:var(--sky)}
.subscribe h2 span{color:var(--blue)}
.subscribe p{position:absolute;left:80px;top:94px;font-size:14px;color:#555}
.subscribe .field{left:572px;top:70px;width:362px;font-size:13px;color:#777}

/* footer */
.site-footer{position:absolute;top:3348px;left:0;width:1200px;height:274px;background:var(--blue)}
.contact-item{position:absolute;top:42px;width:300px;text-align:center;color:var(--white)}
.contact-icon{width:46px;height:46px;margin:0 auto;border:2px solid #6ea8e0;border-radius:50%;display:flex;align-items:center;justify-content:center}
.contact-item h5{margin-top:8px;font-family:'Poppins',sans-serif;font-weight:500;font-size:17px;color:#5fb1ea}
.contact-item div.val{margin-top:4px;font-size:15px;line-height:26px}
.footer-rule{position:absolute;left:80px;top:209px;width:1040px;height:1px;background:rgba(255,255,255,.35)}
.copyright{position:absolute;left:80px;top:230px;font-family:'Poppins',sans-serif;font-size:13.5px;color:var(--white)}
.copyright b{font-weight:600}
.footer-social{position:absolute;left:996px;top:222px;display:flex;gap:6px}
.footer-social i{width:40px;height:40px;border-radius:50%;border:2px solid var(--white);background:var(--white)}
</style>
</head>
<body>

<header class="site-header">
  <div class="brand"><span class="brand-mark"></span><span class="brand-name">QRN</span></div>
  <nav class="main-nav">
    <a class="active" href="#" style="left:483px">Home</a>
    <a href="#" style="left:613px">About Us</a>
    <a href="#" style="left:731px">Services</a>
    <a href="#" style="left:852px">Get A Quote</a>
    <a href="#" style="left:992px">Contact Us</a>
  </nav>
  <svg class="search-icon" width="24" height="24" viewBox="0 0 24 24"><circle cx="10" cy="10" r="7" fill="none" stroke="#0a4f9e" stroke-width="2.6"/><line x1="15" y1="15" x2="22" y2="22" stroke="#0a4f9e" stroke-width="3" stroke-linecap="round"/></svg>
</header>

<section class="hero" role="img" aria-label="Medical team of doctors and staff working together at a laptop">
  <div class="hero-frame"></div>
  <h1 class="hero-title">QUARNELL HEALTH SOLUTIONS LLC</h1>
  <div class="hero-sub">Advancing Health Care</div>
  <a class="btn" href="#">GET A QUOTE</a>
  <div class="hero-dots"><i class="on"></i><i></i><i></i></div>
</section>

<section class="services">
  <h2 class="section-title" style="top:712px"><span>Our</span> Services</h2>
  <p class="services-intro">Lorem Ipsum is simply dummy text of the printing and typesetting industry. Lorem Ipsum has been the industry's standard dummy text ever since the 1500s</p>

  <div class="service-card" style="left:77px;top:903px">
    <div class="service-icon"><svg width="34" height="34" viewBox="0 0 34 34" fill="none" stroke="#fff" stroke-width="2"><circle cx="17" cy="17" r="12"/><path d="M20 12h-4a2.5 2.5 0 0 0 0 5h2a2.5 2.5 0 0 1 0 5h-4M17 9v3M17 22v3"/></svg></div>
    <h3>Revenue Cycle Management</h3>
    <p>Lorem Ipsum is simply dummy text of the printing and typesetting...<a href="#">Read More</a></p>
  </div>
  <div class="service-card" style="left:437px;top:903px">
    <div class="service-icon"><svg width="34" height="34" viewBox="0 0 34 34" fill="none" stroke="#fff" stroke-width="2"><rect x="8" y="5" width="18" height="24"/><path d="M12 11h10M12 16h10M12 21h6"/></svg></div>
    <h3>Medical Billing &amp; Coding</h3>
    <p>Lorem Ipsum is simply dummy text of the printing and typesetting...<a href="#">Read More</a></p>
  </div>
  <div class="service-card" style="left:799px;top:903px">
    <div class="service-icon"><svg width="34" height="34" viewBox="0 0 34 34" fill="none" stroke="#fff" stroke-width="2"><rect x="6" y="8" width="20" height="20"/><path d="M11 18l4 4 13-14"/></svg></div>
    <h3>Regulatory Compliance</h3>
    <p>Lorem Ipsum is simply dummy text of the printing and typesetting...<a href="#">Read More</a></p>
  </div>
  <div class="service-card" style="left:258px;top:1122px">
    <div class="service-icon"><svg width="34" height="34" viewBox="0 0 34 34" fill="#fff"><circle cx="17" cy="13" r="4"/><circle cx="8" cy="15" r="3"/><circle cx="26" cy="15" r="3"/><path d="M10 26a7 7 0 0 1 14 0zM3 25a5 5 0 0 1 8-3v3zM31 25a5 5 0 0 0-8-3v3z"/></svg></div>
    <h3>Human Resources Training</h3>
    <p>Lorem Ipsum is simply dummy text of the printing and typesetting...<a href="#">Read More</a></p>
  </div>
  <div class="service-card" style="left:618px;top:1122px">
    <div class="service-icon"><svg width="34" height="34" viewBox="0 0 34 34" fill="none" stroke="#fff" stroke-width="2"><rect x="5" y="5" width="24" height="18"/><path d="M10 18l5-5 4 3 5-6M12 23l-3 7M22 23l3 7"/></svg></div>
    <h3>Staff Education and Training</h3>
    <p>Lorem Ipsum is simply dummy text of the printing and typesetting...<a href="#">Read More</a></p>
  </div>
</section>

<section class="about">
  <div class="about-photo" role="img" aria-label="Man and woman in office wear reviewing work on a laptop"></div>
  <h2><span>About</span> Quarnell Health Solutions</h2>
  <p style="top:124px">Lorem Ipsum is simply dummy text of the printing and typesetting industry. Lorem Ipsum has been the industry's standard dummy text ever since the 1500s, when an unknown printer took a galley of type and scrambled it to make a type specimen book.</p>
  <p style="top:230px">It has survived not only five centuries, but also the leap into electronic typesetting, remaining essentially unchanged.</p>
  <a class="btn" href="#">READ MORE</a>
</section>

<section class="team">
  <h2 class="section-title" style="top:1820px"><span>Our</span> Team</h2>
  <div class="team-thumb" style="left:362px" role="img" aria-label="Team member portrait"></div>
  <div class="team-thumb" style="left:486px" role="img" aria-label="Team member portrait"></div>
  <div class="team-thumb" style="left:610px" role="img" aria-label="Team member portrait"></div>
  <div class="team-thumb" style="left:736px" role="img" aria-label="Team member portrait"></div>
  <div class="team-photo"><div role="img" aria-label="Selected team member portrait in a dark suit"></div></div>
  <div class="team-card">
    <h4>Member Name</h4>
    <div class="team-social"><i></i><i></i><i></i></div>
    <div class="role">Position</div>
    <p>Lorem Ipsum is simply dummy text of the printing and typesetting industry. Lorem Ipsum has been the industry's</p>
  </div>
</section>

<section class="contact">
  <h2 class="section-title" style="top:58px"><span>Contact</span> Us</h2>
  <div class="field" style="left:225px;top:140px;width:364px">Name*</div>
  <div class="field" style="left:613px;top:140px;width:362px">E-mail*</div>
  <div class="field" style="left:225px;top:194px;width:364px">Phone*</div>
  <div class="field" style="left:613px;top:194px;width:362px">Subject</div>
  <div class="field" style="left:225px;top:246px;width:750px;height:58px">Message</div>
  <a class="btn" href="#">SUBMIT NOW</a>
</section>

<section class="testimonial">
  <h2 class="section-title" style="top:2768px"><span>Client</span> Testimonial</h2>
  <div class="quote-shadow" style="left:322px;top:3110px;width:515px;height:12px;background:#c9e6f5"></div>
  <div class="quote-shadow" style="left:312px;top:3100px;width:535px;height:12px"></div>
  <div class="quote-box">
    <div class="quote-avatar" role="img" aria-label="Client portrait"></div>
    <p>Lorem Ipsum is simply dummy text of the printing and typesetting industry. Lorem Ipsum has been the industry's standard dummy text ever since the 1500s,it to make a type specimen book.</p>
    <div class="author">- Patient Name</div>
  </div>
  <div class="slide-nav" style="left:154px;color:var(--sky)">&#8249;&nbsp; Previous</div>
  <div class="slide-nav" style="left:990px;color:#999">Next &nbsp;&#8250;</div>
</section>

<section class="subscribe">
  <h2>Subscribe <span>Us</span></h2>
  <p>For latest news or updates subscribe our newsletter</p>
  <div class="field">Enter e-mail*</div>
  <svg class="abs" style="left:900px;top:72px" width="22" height="20" viewBox="0 0 22 20"><path d="M1 9L21 1 15 19 11 11z" fill="#0a4f9e"/></svg>
</section>

<footer class="site-footer">
  <div class="contact-item" style="left:89px">
    <div class="contact-icon"><svg width="20" height="20" viewBox="0 0 24 24" fill="none" stroke="#fff" stroke-width="2"><path d="M5 3h4l2 5-3 2a11 11 0 0 0 6 6l2-3 5 2v4a2 2 0 0 1-2 2A18 18 0 0 1 3 5a2 2 0 0 1 2-2z"/></svg></div>
    <h5>Call Us</h5>
    <div class="val">(555) 214-0190</div>
  </div>
  <div class="contact-item" style="left:451px">
    <div class="contact-icon"><svg width="20" height="22" viewBox="0 0 24 26" fill="none" stroke="#fff" stroke-width="2"><path d="M12 24s-8-8-8-14a8 8 0 0 1 16 0c0 6-8 14-8 14z"/><circle cx="12" cy="10" r="3"/></svg></div>
    <h5>Address</h5>
    <div class="val">118 Linden Avenue<br>Riverton, NY 10099</div>
  </div>
  <div class="contact-item" style="left:811px">
    <div class="contact-icon"><svg width="22" height="18" viewBox="0 0 24 18" fill="none" stroke="#fff" stroke-width="2"><rect x="2" y="2" width="20" height="14"/><path d="M2 2l10 8 10-8"/></svg></div>
    <h5>E-mail</h5>
    <div class="val">support@qrn-health.example</div>
  </div>
  <div class="footer-rule"></div>
  <div class="copyright"><b>© QRN QUARNELL HEALTH SOLUTIONS LLC - 2018.</b> All Rights Reserved.</div>
  <div class="footer-social"><i></i><i></i><i></i></div>
</footer>

</body>
</html>
```